Stationery Design Task - Stationary, memo and report templates for professional services company

Looking for someone to update stationary design but just as importantly come up with a template for reports and memos for use in our consulting firm. Would also like some brand use guidelines to be able to share with our whole team. We have an existing logo that we like. Need to update with a more contemporary look so that our deliverables to clients look good and professional yet stylish. This is for business to business communications. No need for envelope design. Important to have design for multiple pages, i.e. first page of a report and then 2nd page. Need to use in MS word documents so must be easy to use and replicate. Don't want something overly complex. Clean, fresh looking is best.

Industry/Entity Type

Information Technology

Font styles to use
Sans Serif

Colors
33a6d7
0792cd
85cae6
cee9f5
cedeed
85abd2
3377b5
0455a3

Requirements
Must have
• Clean look but with a little style or pop. Something that can easily be used in word documents. Need to have page styles that have a first page of a report (not a cover page) and then secondary page.
Nice to have
• - Although the dark blue is our primary color. Might be willing to look at some accent color as well.
Should not have
• Not just our logo on the page with a color bar.

```html
<!DOCTYPE html>
<html lang="en">
<head>
<meta charset="utf-8">
<title>Northvale Systems – Stationery Set</title>
<link rel="stylesheet" href="https://fonts.googleapis.com/css2?family=Roboto:wght@400;500;700&family=Questrial&display=swap">
<style>
  :root {
    --stage: #636363;
    --brand-blue: #0792cd;
    --brand-deep: #0455a3;
    --brand-mid: #3377b5;
    --brand-light: #85cae6;
    --brand-pale: #cee9f5;
    --ink-grey: #666a6e;
    --body-ink: #55595d;
    --paper: #ffffff;
    --paper-shade: #c9c9c9;
    --ghost: #e6e6e6;
  }
  * { box-sizing: border-box; margin: 0; padding: 0; }
  html, body { width: 1200px; height: 578px; overflow: hidden; background: var(--stage); }
  .canvas { position: relative; width: 1200px; height: 578px; }

  .page {
    position: absolute; top: 52px; width: 339px; height: 476px; overflow: hidden;
    background: linear-gradient(180deg, #fbfbfb 0%, #f0f0f0 45%, var(--paper-shade) 100%);
    font-family: "Questrial", sans-serif;
  }
  .page--cover { left: 61px; }
  .page--letter { left: 434px; background: linear-gradient(180deg, #ffffff 0%, #f4f4f4 100%); }
  .page--continuation { left: 806px; background: linear-gradient(90deg, #ffffff 0%, #eeeeee 40%, #f7f7f7 100%); }

  /* cover */
  .cover-pattern {
    position: absolute; top: 0; right: 0; width: 313px; height: 108px;
    background: linear-gradient(90deg, var(--brand-light) 0%, #2f97d3 45%, var(--brand-blue) 100%);
    clip-path: polygon(0 0, 100% 0, 100% 100%, 52% 100%, 22% 60%, 4% 60%);
  }
  .brand {
    position: absolute; display: flex; align-items: center; gap: 12px;
    font-family: "Roboto", sans-serif; font-weight: 700; color: var(--brand-blue);
  }
  .brand__dot { border-radius: 50%; background: var(--brand-blue); flex: none; }
  .brand__name { line-height: 0.95; letter-spacing: 0.5px; }

  .cover-brand { left: 40px; top: 150px; }
  .cover-brand .brand__dot { width: 52px; height: 52px; }
  .cover-brand .brand__name { font-size: 33px; }

  .report-title {
    position: absolute; top: 268px; width: 100%; text-align: center;
    font-family: "Roboto", sans-serif; font-weight: 700; font-size: 30px; color: var(--ink-grey);
  }
  .report-subtitle {
    position: absolute; top: 304px; width: 100%; text-align: center;
    font-family: "Roboto", sans-serif; font-weight: 700; font-size: 10.5px; letter-spacing: 0.4px; color: var(--brand-blue);
  }
  .prepared {
    position: absolute; left: 99px; top: 362px; width: 139px; height: 38px;
    border-top: 1px solid #8a8a8a; border-bottom: 1px solid #8a8a8a; text-align: center;
    font-family: "Roboto", sans-serif;
  }
  .prepared__label { margin-top: 6px; font-weight: 700; font-size: 11.5px; color: var(--ink-grey); }
  .prepared__name { margin-top: 1px; font-weight: 500; font-size: 10px; color: var(--brand-blue); letter-spacing: 0.3px; }

  .footer-band {
    position: absolute; left: 0; top: 445px; width: 100%; height: 14px;
    background: var(--brand-blue); color: #fff; display: flex; align-items: center;
  }
  .cover-dates { justify-content: space-between; padding: 0 28px 0 34px; font-family: "Roboto", sans-serif; font-size: 7.6px; letter-spacing: 0.2px; }

  /* letter */
  .letter-brand { left: 86px; top: 32px; gap: 8px; }
  .letter-brand .brand__dot { width: 34px; height: 34px; }
  .letter-brand .brand__name { font-size: 20px; }

  .ghost-globe {
    position: absolute; border-radius: 50%;
    background: radial-gradient(circle, var(--ghost) 0%, rgba(230,230,230,0.6) 55%, rgba(240,240,240,0) 72%);
  }
  .page--letter .ghost-globe { left: 100px; top: 95px; width: 240px; height: 360px; }

  .letter-body { position: absolute; left: 30px; top: 132px; width: 282px; color: var(--body-ink); }
  .letter-salutation { font-size: 8.4px; margin-bottom: 12px; color: #444; }
  .letter-body p { font-size: 4.7px; line-height: 7.2px; margin-bottom: 5.5px; text-align: justify; }
  .letter-closing { margin-top: 12px; }
  .signature-area {
    position: relative; width: 62px; height: 24px; margin-top: 10px; border-radius: 12px;
    background: linear-gradient(90deg, rgba(51,119,181,0.35), rgba(133,171,210,0.15));
  }
  .letter-contact { justify-content: center; gap: 10px; font-family: "Roboto", sans-serif; font-weight: 700; font-size: 5.4px; letter-spacing: 0.1px; }
  .letter-web {
    position: absolute; top: 465px; width: 100%; text-align: center;
    font-size: 5.6px; letter-spacing: 1.6px; color: var(--brand-blue);
  }

  /* continuation */
  .page--continuation .ghost-globe { left: 60px; top: 90px; width: 300px; height: 380px; }
  .continuation-brand { right: 18px; top: 436px; gap: 5px; }
  .continuation-brand .brand__dot { width: 12px; height: 12px; }
  .continuation-brand .brand__name { font-size: 9px; }
</style>
</head>
<body>
<main class="canvas">

  <section class="page page--cover" aria-label="Report first page">
    <div class="cover-pattern" role="img" aria-label="Blue hexagon tile pattern across the top corner"></div>
    <div class="brand cover-brand">
      <span class="brand__dot"></span>
      <span class="brand__name">NORTHVALE<br>SYSTEMS</span>
    </div>
    <h1 class="report-title">REPORT TITLE</h1>
    <p class="report-subtitle">YOUR SUBTITLE HERE</p>
    <div class="prepared">
      <p class="prepared__label">REPORT PREPARED BY</p>
      <p class="prepared__name">YOUR NAME HERE</p>
    </div>
    <footer class="footer-band cover-dates">
      <span>PROPOSAL ISSUED : SEP 19,2018</span>
      <span>PROPOSAL VALID TO : SEP 19,2019</span>
    </footer>
  </section>

  <section class="page page--letter" aria-label="Letterhead">
    <div class="ghost-globe" role="img" aria-label="Faint hexagon globe watermark"></div>
    <div class="brand letter-brand">
      <span class="brand__dot"></span>
      <span class="brand__name">NORTHVALE<br>SYSTEMS</span>
    </div>
    <article class="letter-body">
      <p class="letter-salutation">Dear Mr. Harlow,</p>
      <p>Thank you for the time you gave our team last week. This letter sums up the points we agreed on during the review and lists the steps we plan to take next. We will send a short draft of the plan before the end of the month so your staff can add notes and raise questions early. Each item below has an owner and a date.</p>
      <p>Our first step is a full audit of the network and the servers at both sites. We will map each device, note its age and check how it is used. After that we can show where money is lost and where simple fixes will give the biggest return for the year ahead.</p>
      <p>The second step covers support and training. Your staff will get clear guides, short sessions and a help desk that answers within one working day. We will track every request, report on trends each quarter and adjust the service as your needs change. Pricing for both steps is set out in the attached proposal, along with the terms and the timeline.</p>
      <p>Please let us know if any part of this letter needs more detail. We are glad to meet again at a time that suits you and look forward to working with your team.</p>
      <p class="letter-closing">Sincerely,</p>
      <div class="signature-area" role="img" aria-label="Handwritten signature of Daniel Harlow"></div>
    </article>
    <footer class="footer-band letter-contact">
      <span>214 ALDER COURT, FAIRVIEW, OREGON 97024</span>
      <span>555 014 2290 | INFO@NORTHVALESYSTEMS.COM</span>
    </footer>
    <p class="letter-web">www.northvalesystems.com</p>
  </section>

  <section class="page page--continuation" aria-label="Report second page">
    <div class="ghost-globe" role="img" aria-label="Faint hexagon globe watermark"></div>
    <div class="brand continuation-brand">
      <span class="brand__dot"></span>
      <span class="brand__name">NORTHVALE</span>
    </div>
  </section>

</main>
</body>
</html>
```